Quimbly Needs a 1 Page Redesign with UI/UX Elements

Quimbly is a GIF creation and sharing site. We are upgrading one of our main responsive website pages. [Please see: http://quimblyzone.net/R-4TzLa for an example]

Need design versions for Desktop, tablet & mobile.

Also need frontend development to implement page. Currently on Foundation framework.

There are many functions/nav elements that need to be on this page in an uncluttered and clear manner. Not all of functions need to be shown at all times. Need a designer with UI/UX background to incorporate these and make it easy to navigate for the user.

The designer needs to be familiar with the site to understand each function. Color scheme will remain the same as current site.

If there are Dropdowns/collapsed or hidden features - need to know how they look when opened.

Target Market(s)

Quimbly has a varied demographic but focuses on under 25.

Coding

Coded - Design and coding required

Number of Pages Required

1 page

Font styles to use
Sans Serif

Requirements
Must have
• The top and bottom nav bars must stay the same. We are not redesigning the whole site yet, just that page.
• This page is developed with sharing in mind. Our top 3 actions are highlighted below. Be creative & think about user experience as our #1 priority
• Desktop
•  SOCIAL SHARE BUTTONS Zentrova/Plinkit/Voxmora/Brolendar
•  Download Button
•  Create a GIF Button
• OTHER FEATURES THAT MUST BE INCLUDED
• Share This With Friends pop up
• Title of GIF
• Added XX days ago by XXXX in XXX
• Source
• Thumbs up votes showing numerically (no down vote thumb)
• Total Views
• Embed Links: direct, website, message board, markdown
• NSFW Flag
• MP4 to GIF toggle
• Next arrows to scroll through GIFs
• Scroll thumbnail bar for like GIFs at the bottom of the page
• NEW FEATURES TO IMPLEMENT
• Favorite (bookmark Option)
• LOGGED IN USERS:
• Logged in users also have Private Button & Delete Button
• MOBILE
• We would like to keep the mobile page as minimalist as possible.
• Download button
• Create a GIF button
• Sharing button: Drovanel, Zentrova, Plinkit, Voxmora,
• Share Via SMS
• (Please incorporate the share buttons in a creative & clean way)
• Three dots that would open up to reveal tags
• Thumbnail scroll at bottom for GIFs in the same category
Nice to have
• Be creative with how the page features are laid out. We want it to be easy for users to navigate & clear what actions are there.
Should not have
• Basically anything that is on the page now. The buttons don't look like buttons & there is no drive to any actions (like sharing). Please see attached file for what NOT to do.

```html
<!DOCTYPE html>
<html lang="en">
<head>
<meta charset="utf-8">
<title>Quimbly – GIF page</title>
<link rel="stylesheet" href="https://fonts.googleapis.com/css2?family=Open+Sans:wght@300;400;600;700&display=swap">
<style>
:root{
  --yellow:#fbe41c;
  --ink:#333333;
  --muted:#666666;
  --page:#e9e9e9;
  --card:#ffffff;
  --dark:#141414;
  --arrow:#e5533a;
  --blue-z:#3b5998;
  --blue-p:#1da1f2;
  --red-v:#e0483e;
  --green-d:#2ecc71;
}
*{margin:0;padding:0;box-sizing:border-box}
html,body{width:743px;height:1200px;overflow:hidden}
body{position:relative;background:var(--page);font-family:'Open Sans',sans-serif;color:var(--ink)}
.abs{position:absolute}
.btn{position:absolute;display:flex;align-items:center;justify-content:center;background:var(--yellow);border-radius:14px;font-size:9px;color:var(--ink)}

/* hero */
.hero{left:0;top:0;width:743px;height:319px;background:radial-gradient(ellipse at 55% 30%,#5a57b0 0%,#2d2a78 40%,#120f2e 80%,#06050f 100%)}
.logo{left:62px;top:16px;display:flex;align-items:center;gap:5px;color:#fff;font-weight:700;font-size:14px}
.logo .mark{width:15px;height:15px;background:var(--yellow);border-radius:2px}
.login{left:502px;top:15px;width:74px;height:21px;border:1px solid #3a3a5a;background:#121226;color:#fff;font-size:7px;display:flex;align-items:center;justify-content:center;gap:6px}
.signup{left:582px;top:15px;width:74px;height:21px;background:var(--yellow);font-size:7px;display:flex;align-items:center;justify-content:center;gap:6px}
.hero-title{left:0;width:743px;top:111px;text-align:center;color:#fff;font-size:16px;font-weight:300;letter-spacing:.3px}
.hero-sub{left:0;width:743px;top:138px;text-align:center;color:#fff;font-size:9.5px}
.hero-cta{left:318px;top:169px;width:107px;height:27px;font-size:9.5px}
.hero-arrow{top:144px;width:24px;height:24px;border-radius:50%;background:rgba(255,255,255,.15)}

/* nav */
.mainnav{left:0;top:319px;width:743px;height:29px;background:var(--yellow)}
.mainnav span{position:absolute;top:10px;font-size:7px;color:var(--ink)}

/* detail */
.gif-title{left:67px;top:383px;font-size:16px;font-weight:400}
.added{left:67px;top:415px;font-size:7px}
.toggle{left:66px;top:439px;width:124px;height:31px;background:#fff;border-radius:16px}
.toggle .mp4{position:absolute;left:12px;top:9px;font-size:9px}
.toggle .gif{position:absolute;left:55px;top:4px;width:66px;height:23px;background:var(--yellow);border-radius:12px;display:flex;align-items:center;justify-content:center;font-size:9px}
.stat{top:487px;font-size:7px;display:flex;align-items:center;gap:4px}
.source-h{left:71px;top:525px;font-size:16px;font-weight:400}
.source-p{left:72px;top:556px;font-size:8.5px}
.video{left:257px;top:377px;width:425px;height:221px;background:linear-gradient(180deg,#4d5f78 0%,#8c8a86 45%,#3a3530 100%)}
.video .bar{position:absolute;left:30px;right:40px;top:203px;height:2px;background:#e8e8e8}

/* share bar */
.sharebar{left:61px;top:638px;width:621px;height:44px;background:#fff}
.sharebar .lbl{position:absolute;left:9px;top:13px;font-size:12px}
.soc{position:absolute;top:10px;width:26px;height:26px;border-radius:50%;color:#fff;font-size:10px;font-weight:600;display:flex;align-items:center;justify-content:center}
.act{top:649px;width:98px;height:25px;font-size:9.5px;gap:6px}

/* features */
.feat-h{left:166px;top:712px;font-size:12px;font-weight:400}
.feat{left:61px;top:740px;width:363px;height:140px;background:#fff}
.row{position:absolute;display:flex;align-items:center;gap:5px;font-size:9.5px}
.row small{font-size:7px}
.row .ar{width:9px;height:8px}
.comments-h{left:497px;width:185px;top:750px;text-align:center;font-size:12px;font-weight:400}
.comment-in{left:497px;top:782px;width:185px;height:20px;background:#f4f4f4;font-size:7px;color:#aaa;padding:6px 12px}
.send{left:498px;top:824px;width:83px;height:18px;font-size:7px}

/* more */
.new-h{left:62px;top:905px;font-size:12.5px;font-weight:400}
.rule{left:62px;top:936px;width:620px;height:1px;background:#d6d6d6}
.pager{left:655px;top:949px;width:26px;height:26px;border-radius:50%;background:#f4f4f4;font-size:10px;display:flex;align-items:center;justify-content:center}
.thumb{top:989px;width:135px;height:107px;border:2px solid #fff}
.meta{top:1102px;width:135px;height:10px}

/* footer */
.footer{left:0;top:1150px;width:743px;height:50px;background:var(--dark)}
.footer .copy{position:absolute;left:62px;top:19px;font-size:7px;color:#fff}
.footer .copy b{color:var(--yellow);font-weight:400}
.footer .follow{position:absolute;left:498px;top:19px;font-size:7px;color:#fff}
.fsoc{position:absolute;top:16px;width:17px;height:17px;border-radius:50%;color:#fff;font-size:7px;display:flex;align-items:center;justify-content:center}
</style>
</head>
<body>

<header class="abs hero" role="img" aria-label="Concert crowd silhouettes with raised hands under purple stage lights"></header>
<div class="abs logo"><span class="mark"></span>Quimbly</div>
<div class="abs login">
  <svg width="7" height="8" viewBox="0 0 7 8"><rect x="0" y="3" width="7" height="5" fill="#fff"/><path d="M1.5 3V2a2 2 0 0 1 4 0v1" stroke="#fff" fill="none"/></svg>LOG IN
</div>
<div class="abs signup">
  <svg width="7" height="8" viewBox="0 0 7 8"><circle cx="3.5" cy="2" r="2" fill="#333"/><path d="M0 8a3.5 3.5 0 0 1 7 0z" fill="#333"/></svg>SIGN UP
</div>
<svg class="abs" style="left:672px;top:22px" width="10" height="10" viewBox="0 0 10 10"><circle cx="4" cy="4" r="3" stroke="#fff" stroke-width="1.5" fill="none"/><path d="M6.5 6.5L9 9" stroke="#fff" stroke-width="1.5"/></svg>
<h1 class="abs hero-title">GIF CREATION AND SHARING SITE</h1>
<p class="abs hero-sub">We are upgrading one of our main responsive website pages.</p>
<div class="btn hero-cta">MAKE A GIF</div>
<svg class="abs hero-arrow" style="left:17px" viewBox="0 0 24 24"><path d="M14 7l-5 5 5 5" stroke="#222" stroke-width="2.5" fill="none"/></svg>
<svg class="abs hero-arrow" style="left:698px" viewBox="0 0 24 24"><path d="M10 7l5 5-5 5" stroke="#222" stroke-width="2.5" fill="none"/></svg>

<nav class="abs mainnav">
  <span style="left:105px">THE GALLERY</span>
  <span style="left:194px">PICTURES TO GIF</span>
  <span style="left:296px">TUBEVIO TO GIF</span>
  <span style="left:398px">UPLOAD A GIF</span>
  <span style="left:490px">VIDEO TO GIF</span>
  <span style="left:580px">WEBCAM TO GIF</span>
</nav>

<h2 class="abs gif-title">LeapcrewZ</h2>
<p class="abs added">Added last week anonymously in <b>FUNNY GIFS</b></p>
<div class="abs toggle"><span class="mp4">MP4</span><span class="gif">GIF</span></div>
<div class="abs stat" style="left:70px">
  <svg width="9" height="6" viewBox="0 0 9 6"><ellipse cx="4.5" cy="3" rx="4.5" ry="3" fill="#222"/><circle cx="4.5" cy="3" r="1.3" fill="#fff"/></svg>140 Total Views
</div>
<div class="abs stat" style="left:168px">
  <svg width="9" height="8" viewBox="0 0 9 8"><rect x="0" y="3" width="2" height="5" fill="#222"/><path d="M3 3l2-3h1v3h3v5H3z" fill="#222"/></svg>224 Likes
</div>
<h3 class="abs source-h">Source</h3>
<p class="abs source-p">Watch the full Tubevio video</p>
<div class="btn" style="left:69px;top:585px;width:131px;height:24px">Create GIF From This Video</div>

<div class="abs video" role="img" aria-label="Video still of a band jumping on a waterfront at sunset">
  <svg class="abs" style="left:198px;top:95px" width="30" height="30" viewBox="0 0 30 30"><circle cx="15" cy="15" r="13" stroke="rgba(255,255,255,.5)" stroke-width="2" fill="none"/><path d="M12 9l9 6-9 6z" fill="rgba(255,255,255,.5)"/></svg>
  <svg class="abs" style="left:12px;top:198px" width="11" height="11" viewBox="0 0 11 11"><circle cx="5.5" cy="5.5" r="4.5" stroke="#fff" fill="none"/><path d="M4.5 3.5l3 2-3 2z" fill="#fff"/></svg>
  <div class="bar"></div>
  <svg class="abs" style="left:390px;top:199px" width="24" height="9" viewBox="0 0 24 9"><path d="M0 3h2l3-3v9L2 6H0z" fill="#fff"/><path d="M16 0h3v1h-2v2h-1zM21 0h3v3h-1V1h-2zM16 6h1v2h2v1h-3zM23 6h1v3h-3V8h2z" fill="#fff"/></svg>
</div>

<div class="abs sharebar">
  <span class="lbl">Social:</span>
  <span class="soc" style="left:56px;background:var(--blue-z)">Z</span>
  <span class="soc" style="left:88px;background:var(--blue-p)">P</span>
  <span class="soc" style="left:120px;background:var(--red-v)">V</span>
  <span class="soc" style="left:152px;background:var(--green-d)">D</span>
</div>
<div class="btn act" style="left:318px;color:#e0492f">
  <svg width="11" height="10" viewBox="0 0 11 10"><path d="M4 0h3v4h2L5.5 7.5 2 4h2z" fill="#222"/><rect x="0" y="8" width="11" height="2" fill="#222"/></svg>Download
</div>
<div class="btn act" style="left:451px;color:#2b7fd6">
  <svg width="10" height="10" viewBox="0 0 10 10"><circle cx="5" cy="5" r="5" fill="#222"/><path d="M5 2.5v5M2.5 5h5" stroke="#fff" stroke-width="1.4"/></svg>More
</div>
<div class="btn act" style="left:584px;color:#3cbf5c">
  <svg width="11" height="10" viewBox="0 0 11 10"><rect x="0.6" y="1.6" width="7.5" height="7.8" stroke="#222" stroke-width="1.2" fill="none"/><path d="M4 6l5.5-5.5 1 1L5 7H4z" fill="#222"/></svg>Create a Gif
</div>

<h3 class="abs feat-h">Features</h3>
<section class="abs feat">
  <div class="row" style="left:19px;top:16px"><svg class="ar" viewBox="0 0 9 8"><path d="M0 8C0 4 2 3 5 3V0l4 4-4 4V5C3 5 1 6 0 8z" fill="var(--arrow)"/></svg>Share <small>- &nbsp;⋖ 122 Shares</small></div>
  <div class="row" style="left:19px;top:36px"><svg class="ar" viewBox="0 0 9 8"><path d="M0 8C0 4 2 3 5 3V0l4 4-4 4V5C3 5 1 6 0 8z" fill="var(--arrow)"/></svg>Title <small>&nbsp;- &nbsp;GIF</small></div>
  <div class="row" style="left:19px;top:59px"><svg class="ar" viewBox="0 0 9 8"><path d="M0 8C0 4 2 3 5 3V0l4 4-4 4V5C3 5 1 6 0 8z" fill="var(--arrow)"/></svg>Added <small>- &nbsp;XX days ago by XXXX in XXX</small></div>
  <div class="row" style="left:19px;top:80px"><svg class="ar" viewBox="0 0 9 8"><path d="M0 8C0 4 2 3 5 3V0l4 4-4 4V5C3 5 1 6 0 8z" fill="var(--arrow)"/></svg>Source <small>- &nbsp;Is a Dummy Text</small></div>
  <div class="row" style="left:19px;top:106px"><svg class="ar" viewBox="0 0 9 8"><path d="M0 8C0 4 2 3 5 3V0l4 4-4 4V5C3 5 1 6 0 8z" fill="var(--arrow)"/></svg>Thumbs <small>- &nbsp;👍︎ 12 Likes</small></div>
  <div class="row" style="left:223px;top:33px"><svg class="ar" viewBox="0 0 9 8"><path d="M0 8C0 4 2 3 5 3V0l4 4-4 4V5C3 5 1 6 0 8z" fill="var(--arrow)"/></svg>Total <small>- &nbsp;◉ 20 Views</small></div>
  <div class="row" style="left:223px;top:54px"><svg class="ar" viewBox="0 0 9 8"><path d="M0 8C0 4 2 3 5 3V0l4 4-4 4V5C3 5 1 6 0 8z" fill="var(--arrow)"/></svg>Links <small>- &nbsp;Direct , Website</small></div>
  <div class="row" style="left:223px;top:76px"><svg class="ar" viewBox="0 0 9 8"><path d="M0 8C0 4 2 3 5 3V0l4 4-4 4V5C3 5 1 6 0 8z" fill="var(--arrow)"/></svg>NSFW <small>- &nbsp;⚑ Flag</small></div>
</section>

<h3 class="abs comments-h">Comments</h3>
<div class="abs comment-in">Add a Comment ...</div>
<div class="btn send">Send a Post</div>

<h3 class="abs new-h">New Features</h3>
<div class="abs rule"></div>
<div class="abs pager">‹ ›</div>

<div class="abs thumb" style="left:62px;background:linear-gradient(160deg,#3c6fa8,#f0b24a 60%,#3a2a20)" role="img" aria-label="Mountain biker jumping at sunset"></div>
<div class="abs thumb" style="left:222px;background:linear-gradient(180deg,#a9c6e6,#5f8a96 55%,#2e5f6c)" role="img" aria-label="Waterfront building and railing"></div>
<div class="abs thumb" style="left:383px;background:linear-gradient(135deg,#f08a3c,#ffffff 40%,#2f9bd6)" role="img" aria-label="Email marketing graphic with phone and envelopes"></div>
<div class="abs thumb" style="left:545px;background:linear-gradient(180deg,#8fc86a,#e8e2dc 55%,#d9b7c0)" role="img" aria-label="Beach wedding arch with flowers"></div>

<svg class="abs meta" style="left:67px" width="135" height="10" viewBox="0 0 135 10"><path d="M5 0l1.5 3.3 3.5.4-2.6 2.4.7 3.5L5 7.8 1.9 9.6l.7-3.5L0 3.7l3.5-.4z" stroke="#e8b800" fill="none"/><path d="M16 0l1.5 3.3 3.5.4-2.6 2.4.7 3.5L16 7.8l-3.1 1.8.7-3.5L11 3.7l3.5-.4z" fill="#e8b800"/><path d="M112 0h7v10l-3.5-3L112 10z" fill="var(--red-v)"/></svg>
<svg class="abs meta" style="left:227px" width="135" height="10" viewBox="0 0 135 10"><path d="M5 0l1.5 3.3 3.5.4-2.6 2.4.7 3.5L5 7.8 1.9 9.6l.7-3.5L0 3.7l3.5-.4z" stroke="#e8b800" fill="none"/><path d="M16 0l1.5 3.3 3.5.4-2.6 2.4.7 3.5L16 7.8l-3.1 1.8.7-3.5L11 3.7l3.5-.4z" fill="#e8b800"/><path d="M112 0h7v10l-3.5-3L112 10z" fill="var(--red-v)"/></svg>
<svg class="abs meta" style="left:388px" width="135" height="10" viewBox="0 0 135 10"><path d="M5 0l1.5 3.3 3.5.4-2.6 2.4.7 3.5L5 7.8 1.9 9.6l.7-3.5L0 3.7l3.5-.4z" stroke="#e8b800" fill="none"/><path d="M16 0l1.5 3.3 3.5.4-2.6 2.4.7 3.5L16 7.8l-3.1 1.8.7-3.5L11 3.7l3.5-.4z" fill="#e8b800"/><path d="M112 0h7v10l-3.5-3L112 10z" fill="var(--red-v)"/></svg>
<svg class="abs meta" style="left:549px" width="135" height="10" viewBox="0 0 135 10"><path d="M5 0l1.5 3.3 3.5.4-2.6 2.4.7 3.5L5 7.8 1.9 9.6l.7-3.5L0 3.7l3.5-.4z" stroke="#e8b800" fill="none"/><path d="M16 0l1.5 3.3 3.5.4-2.6 2.4.7 3.5L16 7.8l-3.1 1.8.7-3.5L11 3.7l3.5-.4z" fill="#e8b800"/><path d="M112 0h7v10l-3.5-3L112 10z" fill="var(--red-v)"/></svg>

<footer class="abs footer">
  <p class="copy"><b>QUIMBLY</b> © 2015 | Privacy Policy</p>
  <p class="follow">Follow Us On:</p>
  <span class="fsoc" style="left:558px;background:#1f7fb5">L</span>
  <span class="fsoc" style="left:584px;background:var(--blue-z)">Z</span>
  <span class="fsoc" style="left:610px;background:#444">G</span>
  <span class="fsoc" style="left:637px;background:var(--blue-p)">P</span>
  <span class="fsoc" style="left:664px;background:#f39c12">R</span>
</footer>

</body>
</html>
```